Lindqor Allied co-marketing flier

We want a flier that our partners (IT consultants) can hand out to their clients and that we can send to local businesses on their behalf to demonstrate that they can help customers purchase a phone system that has professional features that they would expect in a phone solution that costs thousands of dollars.

We want the brochure to look very professional with excellent layout and use of space.

The Lindqor Allied corporate colour is green and more details can be found at www.lindqorallied.example.au.

We have attached a draft Word document that contains most of the information we need but please present the information in the way YOU believe it should be laid out.

We are looking for a designer who understands the concept and uses their own skills to produce a work of art.

Target Market(s)

small businesses that want to save money but also want a modern phone with lots of features

Industry/Entity Type

Marketing

Requirements
Must have
• Must have an image of the main phone and a cordless handset to indicate that they don't need wires to set the system up.

Must have our logo and website address

Must have a box or some "placeholder" where our partners can stamp or insert their details.

Must have a "call to action" saying "Contact us for a quote"

```html
<!DOCTYPE html>
<html lang="en">
<head>
<meta charset="utf-8">
<title>Lindqor Allied – Phone System Flier</title>
<link rel="stylesheet" href="https://fonts.googleapis.com/css2?family=Alegreya:wght@400;700&family=Oswald:wght@500;600&family=Arimo:wght@700&display=swap">
<style>
  :root {
    --green: #2f8f2c;
    --green-bright: #3aa536;
    --green-deep: #1f5c24;
    --headline-green: #1d5a28;
    --charcoal: #2b2b2b;
    --ink: #231f20;
    --white: #ffffff;
    --phone-grey: #c9cbcd;
    --phone-dark: #3a3c3e;
  }
  * { box-sizing: border-box; margin: 0; padding: 0; }
  html, body { width: 848px; height: 1200px; overflow: hidden; background: var(--white); }
  .flier { position: relative; width: 848px; height: 1200px; overflow: hidden; background: var(--white); }

  .backdrop { position: absolute; inset: 0; }

  .quote-corner {
    position: absolute; left: 20px; top: 8px; color: var(--white);
    font-family: "Oswald", "Arial Narrow", sans-serif;
  }
  .quote-corner__cta { font-size: 27px; font-weight: 600; line-height: 1.3; }
  .quote-corner__details { margin-top: 14px; font-size: 17px; font-weight: 500; line-height: 1.4; }

  .brand {
    position: absolute; left: 46px; top: 228px;
    font-family: "Alegreya", Georgia, serif; font-weight: 700;
    font-size: 46px; color: var(--green); letter-spacing: 0.5px;
  }

  .divider {
    position: absolute; left: 386px; top: 30px; height: 296px;
    border-left: 1px dotted #bdbdbd;
  }

  .product-shot {
    position: absolute; left: 402px; top: 40px; width: 384px; height: 272px;
    border-radius: 18px;
    background: radial-gradient(ellipse at 55% 45%, #e4e5e6 0%, var(--phone-grey) 55%, var(--phone-dark) 100%);
  }

  .headline {
    position: absolute; left: 0; width: 848px; text-align: center;
    font-family: "Alegreya", Georgia, serif;
  }
  .headline--question { top: 354px; font-size: 41px; color: var(--ink); }
  .headline--answer { top: 442px; font-size: 58px; color: var(--headline-green); }

  .pitch {
    position: absolute; left: 170px; width: 660px; top: 636px; text-align: center;
    font-family: "Alegreya", Georgia, serif; font-size: 32px; line-height: 43px;
    color: var(--white);
  }
  .pitch strong { font-weight: 700; }

  .features {
    position: absolute; left: 42px; top: 852px; color: var(--white);
    font-family: "Arimo", Arial, sans-serif; font-weight: 700;
  }
  .features__title { font-size: 22px; margin-bottom: 30px; }
  .features__list { list-style: none; font-size: 18px; line-height: 27.5px; }
  .features__list li { position: relative; padding-left: 73px; }
  .features__list li::before {
    content: ""; position: absolute; left: 3px; top: 6px;
    width: 13px; height: 13px; border: 1.5px solid var(--white);
  }
  .features__note { display: block; padding-left: 6px; }
</style>
</head>
<body>
<main class="flier">
  <svg class="backdrop" width="848" height="1200" viewBox="0 0 848 1200" aria-hidden="true">
    <defs>
      <radialGradient id="greenGlow" cx="0.35" cy="0.55" r="0.7">
        <stop offset="0" stop-color="var(--green-bright)"/>
        <stop offset="0.7" stop-color="var(--green)"/>
        <stop offset="1" stop-color="var(--green-deep)"/>
      </radialGradient>
      <radialGradient id="cornerGlow" cx="0.3" cy="0.6" r="0.8">
        <stop offset="0" stop-color="var(--green-bright)"/>
        <stop offset="1" stop-color="var(--green-deep)"/>
      </radialGradient>
    </defs>
    <path d="M0 0 H335 C350 60 330 120 270 150 C200 185 90 185 0 185 Z" fill="url(#cornerGlow)"/>
    <path d="M0 820 C120 640 330 548 560 548 C700 548 800 590 848 620 V1200 H0 Z" fill="url(#greenGlow)"/>
    <path d="M0 800 C140 770 330 790 470 860 C560 905 620 980 640 1200 H0 Z" fill="var(--charcoal)" opacity="0.85"/>
    <path d="M0 800 C120 780 260 800 360 840 C230 830 120 860 0 900 Z" fill="url(#greenGlow)" opacity="0.6"/>
    <path d="M450 1200 C500 1010 640 880 848 865 V1200 Z" fill="var(--charcoal)"/>
  </svg>

  <header class="quote-corner">
    <p class="quote-corner__cta">Contact us for a Quote</p>
    <p class="quote-corner__details">corvane (Meridel Group Pty Ltd)<br>ABN: 52 604 318 907<br>www.lindqorallied.example.au</p>
  </header>

  <p class="brand">Lindqor Allied</p>
  <div class="divider"></div>
  <div class="product-shot" role="img" aria-label="Photo of a black and silver desk phone with colour display and coiled handset"></div>

  <h1 class="headline headline--question">Looking for a new phone system?</h1>
  <h2 class="headline headline--answer">It's cheaper than you think.</h2>

  <p class="pitch">Our proven <strong>VoIP solution</strong> comes with all the professional features to service an office of up to 6 people.</p>

  <section class="features">
    <h3 class="features__title">Features include, but not limited, to:</h3>
    <ul class="features__list">
      <li>very low line rental rates*</li>
      <li>10c local and national calls untimed</li>
      <li>voicemail-to-email</li>
      <li>Bluetooth-to-mobile</li>
      <li>direct in-dial to every extension</li>
      <li>number portability<span class="features__note">(keep your number when you move)</span></li>
      <li>call records via spreadsheet</li>
      <li>flat rate local and national calls</li>
    </ul>
  </section>
</main>
</body>
</html>
```